Stylish Business Cards Wanted

- DOUBLE SIDED Design Required -

High end, edgy cards for a corporate and personal stylist. Must include logo,
Name: Belinda Harwick
Title: Director and Stylist
telephone : +61 8 7142 5809
email: belinda@theloombriefing.example
website: theloombriefing.example
Tag: Corporate Workwear & Uniform Specialist | Personal Stylist
Would like nice icons for telephone, email, website

Target Market(s)

Businesses wanting stylish uniforms, people wanting stylish wardrobes

Industry/Entity Type

Corporate Workwear Stylist

Contact Information for Business Card

I would like black, white and gold foiling incorporated in the design - possibly a touch of the other colours on my branding guide attached Name: Belinda Harwick Title: Director and Stylist telephone : +61 8 7142 5809 email: belinda@theloombriefing.example website: theloombriefing.example Tag: Corporate Workwear & Uniform Specialist | Personal Stylist Would like nice icons for telephone, email, website

Font styles to use
Other font styles liked:
• Raleway

Colors

Designer to choose colors to be used in the design.

Requirements
Must have
• Gold foil accents

```html
<!DOCTYPE html>
<html lang="en">
<head>
<meta charset="utf-8">
<title>The Loom Briefing – Business Cards</title>
<link rel="stylesheet" href="https://fonts.googleapis.com/css2?family=Berkshire+Swash&family=Raleway:wght@400;500;600&display=swap">
<style>
  :root {
    --stage: #2e2e2e;
    --card-white: #ffffff;
    --card-black: #221f20;
    --gold: #e2b84f;
    --ink: #1f1d1e;
    --silver: #dfe1e0;
    --ghost: #ececec;
    --rule: #c9c9c9;
  }
  * { margin: 0; padding: 0; box-sizing: border-box; }
  html, body { width: 1200px; height: 866px; overflow: hidden; }
  body {
    background: var(--stage);
    font-family: "Raleway", sans-serif;
    position: relative;
  }
  .card {
    position: absolute;
    left: 250px;
    width: 700px;
    height: 400px;
    overflow: hidden;
    box-shadow: 0 10px 24px rgba(0,0,0,.45);
  }
  .card--front { top: 24px; background: var(--card-white); }
  .card--back { top: 442px; background: var(--card-black); }

  .ghost-name {
    position: absolute;
    left: 34px; top: 22px;
    font-family: "Raleway", sans-serif;
    font-weight: 500;
    font-size: 54px;
    letter-spacing: 4px;
    line-height: 1.05;
    color: var(--ghost);
    text-transform: uppercase;
  }
  .contact {
    position: absolute;
    left: 52px; top: 150px;
  }
  .contact__name {
    font-family: "Berkshire Swash", cursive;
    font-size: 34px;
    color: var(--gold);
    line-height: 1.1;
  }
  .contact__title {
    font-size: 19px;
    color: var(--ink);
    margin: 2px 0 14px;
  }
  .contact__list { list-style: none; }
  .contact__item {
    display: flex; align-items: center; gap: 10px;
    font-size: 18px; color: var(--ink);
    line-height: 1.5;
    white-space: nowrap;
  }
  .contact__icon { width: 16px; height: 16px; flex: none; }
  .front-rule {
    position: absolute;
    left: 340px; right: 40px; top: 314px;
    border-top: 1px solid var(--rule);
  }
  .wordmark {
    position: absolute;
    display: flex; align-items: center; gap: 12px;
    font-family: "Raleway", sans-serif;
    font-weight: 600;
    text-transform: uppercase;
    letter-spacing: 5px;
    line-height: 1.1;
    white-space: nowrap;
  }
  .wordmark__dot { width: 14px; height: 14px; flex: none; }
  .wordmark--front { right: 44px; top: 168px; font-size: 30px; color: var(--ink); }
  .wordmark--front .wordmark__dot { background: var(--ink); }
  .wordmark--back { right: 60px; top: 96px; font-size: 44px; color: var(--silver); }
  .wordmark--back .wordmark__dot { background: var(--silver); width: 18px; height: 18px; }

  .tag-band {
    position: absolute;
    left: 0; top: 262px;
    height: 46px;
    background: var(--gold);
    display: inline-flex; align-items: center;
    padding: 0 32px 0 30px;
    font-size: 19px; font-weight: 500;
    color: var(--ink);
    white-space: nowrap;
  }
  .tag-band__sep { margin: 0 12px; }
</style>
</head>
<body>

<section class="card card--front" aria-label="Business card front">
  <div class="ghost-name" aria-hidden="true">The Loom<br>Briefing</div>

  <div class="contact">
    <p class="contact__name">Belinda Harwick</p>
    <p class="contact__title">Director and Stylist</p>
    <ul class="contact__list">
      <li class="contact__item">
        <svg class="contact__icon" viewBox="0 0 16 16" aria-hidden="true"><path d="M4 1.5 6.5 4 5 6c1 2 3 4 5 5l2-1.5 2.5 2.5-2 2C8 14 2 8 2 3.5z" fill="none" stroke="#e2b84f" stroke-width="1.5" stroke-linejoin="round"/></svg>
        +61 8 7142 5809
      </li>
      <li class="contact__item">
        <svg class="contact__icon" viewBox="0 0 16 16" aria-hidden="true"><rect x="1" y="3" width="14" height="10" fill="#e2b84f"/><path d="M1 3l7 6 7-6" fill="none" stroke="#fff" stroke-width="1.3"/></svg>
        belinda@theloombriefing.example
      </li>
      <li class="contact__item">
        <svg class="contact__icon" viewBox="0 0 16 16" aria-hidden="true"><g fill="none" stroke="#e2b84f" stroke-width="1.3"><circle cx="8" cy="8" r="6.5"/><ellipse cx="8" cy="8" rx="3" ry="6.5"/><path d="M1.5 8h13M3 4.5h10M3 11.5h10"/></g></svg>
        theloombriefing.example
      </li>
    </ul>
  </div>

  <div class="front-rule"></div>

  <div class="wordmark wordmark--front">
    <span class="wordmark__dot"></span>
    <span>The Loom<br>Briefing</span>
  </div>
</section>

<section class="card card--back" aria-label="Business card back">
  <div class="wordmark wordmark--back">
    <span class="wordmark__dot"></span>
    <span>The Loom<br>Briefing</span>
  </div>
  <div class="tag-band">
    Corporate Workwear &amp; Uniform Specialist<span class="tag-band__sep">•</span>Personal Stylist
  </div>
</section>

</body>
</html>
```